Fenwick Grading LTD - website for irrigation & Landscape Lighting & Buried service wire

Looking for a website to help promote my business with Irrigation (installation, service, etc) and buried service wire/drainage solutions.

Commercial/Residential

Landscape lighting.

I’ll get photos in the trucks and trailers to upload as well maybe the machine as well.

Target Market(s)

Homeowners who want green grass and beautiful gardens. Beautiful landscape lighting

Industry/Entity Type

Irrigation systems and landscape lighting and buried service wire to homes and offering Drainage soltions.

Coding

Coded - Design and coding required

Number of Pages Required

4 page

Colors
F0912C
F2A743
F7CA91
FBE8D2
FDF5EE

Requirements
Must have
• was hoping to link up my email on fenwickgrading@mailbox-example.net with the website if possible.
Nice to have
• Page for Irrigation, page for landscape lighting, page buried service wire & drainage soltions.

```html
<!DOCTYPE html>
<html lang="en">
<head>
<meta charset="utf-8">
<title>Fenwick Grading LTD</title>
<link href="https://fonts.googleapis.com/css2?family=Poppins:wght@400;500;600;700&family=Josefin+Sans:wght@700&display=swap" rel="stylesheet">
<style>
:root{
  --orange:#F0912C;
  --orange-2:#F2A743;
  --peach:#F7CA91;
  --cream:#FBE8D2;
  --ivory:#FDF5EE;
  --grey:#959C9C;
  --ink:#333;
  --muted:#555;
  --white:#fff;
}
*{margin:0;padding:0;box-sizing:border-box}
html,body{width:1200px;height:4167px;overflow:hidden}
body{position:relative;font-family:"Poppins",sans-serif;color:var(--ink);background:var(--white)}
.abs{position:absolute}
.heading{position:absolute;font-family:"Josefin Sans",sans-serif;font-weight:700;color:var(--orange);font-size:38px;letter-spacing:2px;display:flex;align-items:center;gap:10px;white-space:nowrap}
.heading::before,.heading::after{content:"";width:42px;height:4px;background:currentColor}
.heading.center{left:0;right:0;justify-content:center}
.btn{position:absolute;display:flex;align-items:center;justify-content:center;font-weight:600;letter-spacing:1px;text-transform:uppercase;clip-path:polygon(8% 0,100% 0,92% 100%,0 100%)}
.photo{position:absolute}

/* top bar */
.topbar{left:0;top:0;width:1200px;height:42px;background:var(--orange);color:var(--white);font-size:13px}
.topbar .item{position:absolute;top:12px;display:flex;align-items:center;gap:10px}
/* header */
.nav a{position:absolute;top:96px;font-size:14px;color:var(--ink);text-decoration:none}
.nav a.active{color:var(--orange)}
.brand{left:480px;top:92px;width:240px;text-align:center;color:var(--orange);font-weight:600;line-height:1}
.brand .name{font-size:38px;display:block}
.brand .sub{font-size:19px;letter-spacing:2px;color:#7b7b7b;display:block;margin-top:4px}
.brand .mark{display:block;width:18px;height:18px;background:var(--orange);margin:0 auto 8px}

/* hero */
.hero-photo{left:0;top:170px;width:1200px;height:650px;background:linear-gradient(180deg,#1d2b3d 0%,#2c3a4a 40%,#6a4a2c 75%,#2b2a22 100%)}
.hero-title{left:0;right:0;top:398px;text-align:center;color:var(--white);font-family:"Josefin Sans",sans-serif;font-weight:700;font-size:35px;line-height:52px;letter-spacing:2px}
.hero-btn{left:518px;top:584px;width:165px;height:36px;background:var(--white);color:var(--orange);font-size:15px}

/* about */
.about-text{left:110px;top:955px;width:470px;font-size:15.5px;line-height:31px;color:var(--muted)}
.about-btn{left:110px;top:1143px;width:165px;height:40px;background:var(--orange);color:var(--white);font-size:16px}
.about-frame{left:648px;top:870px;width:452px;height:285px;background:var(--orange);border-radius:14px}
.about-photo{left:629px;top:880px;width:462px;height:275px;border-radius:12px;background:linear-gradient(160deg,#2f4a2a,#4f6a3a 50%,#8a6a30 80%,#25301e)}

/* services */
.card{position:absolute;width:222px;height:290px;border-radius:6px;color:var(--white);text-align:center;padding-top:68px}
.card.orange{background:var(--orange)}
.card.grey{background:var(--grey)}
.card .icon{position:absolute;left:56px;top:-56px;width:110px;height:110px;border-radius:50%;background:var(--white);border:5px solid currentColor;display:flex;align-items:center;justify-content:center}
.card.orange .icon{border-color:var(--orange)}
.card.grey .icon{border-color:var(--grey)}
.card h3{font-family:"Josefin Sans",sans-serif;font-size:21px;letter-spacing:1px;margin-bottom:8px}
.card p{font-size:13.5px;line-height:26px;padding:0 18px;color:#fde6cc}
.card.grey p{color:#eef0f0}
.card .more{position:relative;margin:12px auto 0;width:120px;height:28px;background:var(--white);font-size:11.5px;font-weight:500;letter-spacing:.5px}
.card.orange .more{color:var(--orange)}
.card.grey .more{color:var(--grey)}
.arrow{position:absolute;width:36px;height:36px;border:2px solid var(--orange);border-radius:50%;display:flex;align-items:center;justify-content:center}

/* testimonials */
.testi-bg{left:0;top:1856px;width:1200px;height:620px;background:var(--cream)}
.review{position:absolute;top:2028px;width:300px;height:257px;background:var(--white);border-radius:4px;box-shadow:0 3px 10px rgba(0,0,0,.08);padding:20px 30px}
.review .avatar{position:absolute;left:30px;top:20px;width:54px;height:54px;border-radius:50%;background:linear-gradient(135deg,#c9a58a,#6b4b3a)}
.review .who{margin-left:63px;font-size:18px;font-weight:500;margin-top:8px}
.review .when{margin-left:63px;font-size:12px;color:var(--muted)}
.review .stars{margin-top:10px;color:var(--orange-2);font-size:16px;letter-spacing:1px}
.review .quote{margin-top:8px;font-size:12.5px;line-height:26px;color:var(--ink)}

/* gallery */
.tile{position:absolute;width:242px;height:178px;border:4px solid var(--white)}
.view-btn{left:540px;top:2952px;width:165px;height:38px;background:var(--white);color:var(--orange);font-size:15px}

/* contact */
.contact-bg{left:0;top:3072px;width:1200px;height:760px;background:linear-gradient(135deg,#f6f6f6,#ececec 50%,#f8f8f8)}
.form-back{left:119px;top:3518px;width:397px;height:132px;background:var(--orange);border-radius:12px}
.form-dot{left:405px;top:3210px;width:108px;height:108px;border-radius:50%;background:var(--peach)}
.form-card{left:138px;top:3230px;width:359px;height:404px;background:var(--white);border-radius:12px;padding:28px 29px}
.form-card h4{font-size:15px;font-weight:500;margin-bottom:18px}
.field{position:relative;border-bottom:1.5px solid #555;height:48px;margin-bottom:14px}
.field label{display:block;font-size:13.5px;color:var(--ink)}
.field span{display:block;font-size:10px;color:var(--muted);margin-top:2px}
.field svg{position:absolute;right:10px;top:14px}
.field.tall{height:90px}
.talk{position:absolute;right:14px;bottom:26px;width:122px;height:26px;background:var(--orange);color:var(--white);font-size:12px;clip-path:polygon(10% 0,100% 0,90% 100%,0 100%);display:flex;align-items:center;justify-content:center;font-weight:600}
.contact-frame{left:638px;top:3298px;width:469px;height:287px;background:var(--orange);border-radius:14px}
.contact-photo{left:646px;top:3308px;width:448px;height:270px;border-radius:10px;background:linear-gradient(120deg,#3b4a5c,#cfd6d8 45%,#eef1f1 70%,#b0b8bc)}

/* footer */
.foot-brand{left:112px;top:3945px;color:var(--white);font-weight:600;line-height:1}
.foot-brand .name{font-size:52px;display:block}
.foot-brand .sub{font-size:26px;letter-spacing:3px;display:block;margin-top:4px}
.foot-brand .mark{display:block;width:24px;height:24px;background:var(--white);margin:0 0 14px 100px}
.social{position:absolute;top:4060px;width:26px;height:26px;border-radius:50%;border:2px solid var(--white)}
.fcol{position:absolute;top:3912px;color:var(--white)}
.fcol h5{font-size:20px;font-weight:600;letter-spacing:.5px;margin-bottom:12px}
.fcol li{list-style:none;font-size:15px;line-height:31px}
.fcol .ci{display:flex;align-items:center;gap:12px;line-height:40px}
.foot-rule{left:112px;top:4122px;width:976px;height:1px;background:rgba(255,255,255,.7)}
.copy{left:0;right:0;top:4133px;text-align:center;color:var(--white);font-size:16px;letter-spacing:.5px}
</style>
</head>
<body>

<!-- top bar -->
<div class="abs topbar">
  <div class="item" style="left:110px">
    <svg width="24" height="16" viewBox="0 0 24 16" fill="none" stroke="#fff" stroke-width="1.6"><rect x="1" y="1" width="22" height="14"/><path d="M1 1l11 8 11-8"/></svg>
    fenwickgrading@mailbox-example.net
  </div>
  <div class="item" style="left:500px">
    <svg width="18" height="18" viewBox="0 0 24 24" fill="none" stroke="#fff" stroke-width="1.8"><path d="M5 3h4l2 5-3 2a11 11 0 006 6l2-3 5 2v4a2 2 0 01-2 2A17 17 0 013 5a2 2 0 012-2z"/></svg>
    Call us (+088) 555-0142
  </div>
  <div class="item" style="left:886px">
    <svg width="18" height="18" viewBox="0 0 24 24" fill="none" stroke="#fff" stroke-width="1.8"><circle cx="12" cy="12" r="10"/><path d="M12 6v6l4 2"/></svg>
    Mon - Sat : 08.00-21.00
  </div>
</div>

<!-- header -->
<nav class="nav">
  <a class="active" style="left:112px">Home</a>
  <a style="left:182px">About Us</a>
  <a style="left:272px">Fiber Optic installation</a>
  <a style="left:794px">Landscape Lighting</a>
  <a style="left:962px">Irrigation Installs</a>
</nav>
<div class="abs brand" style="top:56px">
  <span class="mark"></span>
  <span class="name">FENWICK</span>
  <span class="sub">GRADING LTD</span>
</div>

<!-- hero -->
<div class="photo hero-photo" role="img" aria-label="Modern timber house at dusk with warm landscape lighting"></div>
<svg class="abs" style="left:0;top:720px" width="1200" height="100" viewBox="0 0 1200 100">
  <path d="M0 18 Q360 10 740 100 L1200 15 L1200 100 L0 100Z" fill="#fff"/>
  <path d="M600 60 Q680 55 740 100 L600 100Z" fill="#fff"/>
  <path d="M740 100 L1200 15 L1200 50 L780 100Z" fill="var(--orange)"/>
</svg>
<div class="abs hero-title">HOMEOWNERS WHO WANT GREEN GRASS AND<br>BEAUTIFUL GARDENS.<br>BEAUTIFUL LANDSCAPE LIGHTING</div>
<div class="btn hero-btn">Book Now</div>

<!-- about -->
<div class="heading" style="left:110px;top:890px">ABOUT US</div>
<p class="abs about-text">Lorem Ipsum is simply dummy text of the printing and typesetting industry. Lorem Ipsum has been the industry's standard dummy text ever since the 1500s, when an unknown printer took a galley of type and scrambled it to make a type specimen book</p>
<div class="btn about-btn">Read More</div>
<div class="abs about-frame"></div>
<div class="photo about-photo" role="img" aria-label="Garden path with low bollard lights among ornamental grasses"></div>
<svg class="abs" style="left:0;top:1150px" width="1200" height="130" viewBox="0 0 1200 130">
  <defs><linearGradient id="sweep" x1="0" x2="1"><stop offset="0" stop-color="#F7CA91" stop-opacity=".3"/><stop offset=".5" stop-color="#F2A743"/><stop offset="1" stop-color="#F0912C"/></linearGradient></defs>
  <path d="M0 125 Q300 110 520 95 L700 60 L900 40 L1200 10 L1200 128 L0 128Z" fill="url(#sweep)"/>
</svg>

<!-- services -->
<div class="heading center" style="top:1330px">OUR SERVICES</div>
<div class="arrow" style="left:38px;top:1532px"><svg width="12" height="12" viewBox="0 0 12 12" fill="none" stroke="var(--orange)" stroke-width="2"><path d="M8 1L3 6l5 5"/></svg></div>
<div class="arrow" style="left:1126px;top:1532px"><svg width="12" height="12" viewBox="0 0 12 12" fill="none" stroke="var(--orange)" stroke-width="2"><path d="M4 1l5 5-5 5"/></svg></div>

<div class="card orange" style="left:111px;top:1405px">
  <div class="icon"><svg width="40" height="46" viewBox="0 0 40 46" fill="none" stroke="var(--orange)" stroke-width="2"><rect x="4" y="4" width="32" height="40"/><path d="M10 12h6M22 12h6M10 20h6M22 20h6M10 28h6M22 28h6M16 44v-8h8v8"/></svg></div>
  <h3>COMMERCIAL</h3>
  <p>Lorem Ipsum is simply dummy text of the printing and typesetting industry. Lorem Ipsum has been the industry's.</p>
  <div class="btn more">Read More</div>
</div>
<div class="card grey" style="left:364px;top:1482px">
  <div class="icon"><svg width="50" height="44" viewBox="0 0 50 44" fill="none" stroke="var(--grey)" stroke-width="2"><path d="M4 22L25 4l21 18M10 18v22h30V18M20 40V28h10v12"/></svg></div>
  <h3>RESIDENTIAL</h3>
  <p>Lorem Ipsum is simply dummy text of the printing and typesetting industry. Lorem Ipsum has been the industry's.</p>
  <div class="btn more">Read More</div>
</div>
<div class="card orange" style="left:615px;top:1482px">
  <div class="icon"><svg width="40" height="46" viewBox="0 0 40 46" fill="none" stroke="var(--orange)" stroke-width="2"><circle cx="20" cy="14" r="6"/><path d="M20 2v3M8 14H5M35 14h-3M11 5l2 2M29 5l-2 2M6 26l14 6 14-6v14l-14 6-14-6z M20 32v14"/></svg></div>
  <h3>LIGHTING</h3>
  <p>Lorem Ipsum is simply dummy text of the printing and typesetting industry. Lorem Ipsum has been the industry's.</p>
  <div class="btn more">Read More</div>
</div>
<div class="card grey" style="left:867px;top:1405px">
  <div class="icon"><svg width="50" height="46" viewBox="0 0 50 46" fill="none" stroke="var(--grey)" stroke-width="2"><circle cx="25" cy="8" r="4"/><circle cx="12" cy="14" r="4"/><circle cx="38" cy="14" r="4"/><path d="M25 12v32M12 18c0 10 8 12 8 26M38 18c0 10-8 12-8 26M6 44h38"/></svg></div>
  <h3>FIBER OPTIC</h3>
  <p>Lorem Ipsum is simply dummy text of the printing and typesetting industry. Lorem Ipsum has been the industry's.</p>
  <div class="btn more">Read More</div>
</div>

<!-- testimonials -->
<div class="abs testi-bg"></div>
<div class="heading center" style="top:1935px">OUR TESTIMONIALS</div>
<div class="arrow" style="left:38px;top:2139px"><svg width="12" height="12" viewBox="0 0 12 12" fill="none" stroke="var(--orange)" stroke-width="2"><path d="M8 1L3 6l5 5"/></svg></div>
<div class="arrow" style="left:1126px;top:2139px"><svg width="12" height="12" viewBox="0 0 12 12" fill="none" stroke="var(--orange)" stroke-width="2"><path d="M4 1l5 5-5 5"/></svg></div>

<div class="review" style="left:113px">
  <div class="avatar" role="img" aria-label="Customer portrait"></div>
  <div class="who">Marcus Reed</div><div class="when">10 Days ago</div>
  <div class="stars">★★★★★</div>
  <p class="quote">"Whether it's courses, books, live events, physical products... literally any business I have a stake in needs what they want faster, and increases your profits and business revenue."</p>
</div>
<div class="review" style="left:451px">
  <div class="avatar" role="img" aria-label="Customer portrait"></div>
  <div class="who">Marcus Reed</div><div class="when">10 Months ago</div>
  <div class="stars">★★★★★</div>
  <p class="quote">"Whether it's courses, books, live events, physical products... literally any business I have a stake in needs what they want faster, and increases your profits and business revenue."</p>
</div>
<div class="review" style="left:789px">
  <div class="avatar" role="img" aria-label="Customer portrait"></div>
  <div class="who">Marcus Reed</div><div class="when">1 Years ago</div>
  <div class="stars">★★★★★</div>
  <p class="quote">"Whether it's courses, books, live events, physical products... literally any business I have a stake in needs what they want faster, and increases your profits and business revenue."</p>
</div>

<!-- gallery -->
<svg class="abs" style="left:0;top:2370px" width="1200" height="705" viewBox="0 0 1200 705">
  <path d="M0 100 L485 8 L600 24 L1200 40 L1200 705 L0 705Z" fill="#B96A22"/>
  <path d="M0 100 L485 30 L1200 40 L1200 705 L0 705Z" fill="var(--orange)"/>
  <path d="M0 100 L485 30 L1200 40 L1200 160 L700 100Z" fill="var(--orange-2)" opacity=".35"/>
</svg>
<div class="heading center" style="top:2455px;color:var(--white)">OUR GALLERY</div>
<div class="tile" style="left:65px;top:2530px;background:linear-gradient(160deg,#38506a,#3f6a3a 60%,#6a7a4a)" role="img" aria-label="Lit garden path at dusk"></div>
<div class="tile" style="left:340px;top:2530px;background:linear-gradient(180deg,#bcd4ea,#f2f2f0 50%,#4e8fb0)" role="img" aria-label="White modern villa with pool"></div>
<div class="tile" style="left:615px;top:2530px;background:linear-gradient(180deg,#9cc2e8,#4a6a9a 60%,#7cb03a)" role="img" aria-label="Glass office building with lawn"></div>
<div class="tile" style="left:892px;top:2530px;background:linear-gradient(180deg,#8aa8c8,#d8d0c4 50%,#6a7a5a)" role="img" aria-label="Two-storey family home"></div>
<div class="tile" style="left:65px;top:2727px;background:linear-gradient(160deg,#1f2a4a,#8a5a2a 60%,#e0a050)" role="img" aria-label="Bollard light beside steps at night"></div>
<div class="tile" style="left:340px;top:2727px;background:linear-gradient(180deg,#9aa8b8,#6a5a4a 60%,#b8b8b4)" role="img" aria-label="Commercial building entrance"></div>
<div class="tile" style="left:615px;top:2727px;background:linear-gradient(180deg,#1a1f1a,#3a3a2a 60%,#2a3020)" role="img" aria-label="Outdoor dining area under string lights"></div>
<div class="tile" style="left:892px;top:2727px;background:linear-gradient(180deg,#5a90d0,#a8c0d8 60%,#9a9a9a)" role="img" aria-label="Office towers under blue sky"></div>
<div class="btn view-btn">View All</div>

<!-- contact -->
<div class="abs contact-bg"></div>
<div class="heading center" style="top:3152px">CONTACT US</div>
<div class="abs form-back"></div>
<div class="abs form-dot"></div>
<div class="abs form-card">
  <h4>Send Us A Message</h4>
  <div class="field"><label>Name</label><span>Lawin</span>
    <svg width="16" height="16" viewBox="0 0 24 24" fill="none" stroke="#333" stroke-width="1.8"><circle cx="12" cy="12" r="10"/><circle cx="12" cy="10" r="3"/><path d="M6 19c2-3 10-3 12 0"/></svg></div>
  <div class="field"><label>Email</label><span>lawin@mailbox-example.net</span>
    <svg width="16" height="14" viewBox="0 0 24 18" fill="none" stroke="#333" stroke-width="1.8"><rect x="1" y="1" width="22" height="16"/><path d="M1 1l11 8 11-8"/></svg></div>
  <div class="field"><label>Phone Number</label><span>+88</span>
    <svg width="16" height="16" viewBox="0 0 24 24" fill="none" stroke="#333" stroke-width="1.8"><path d="M5 3h4l2 5-3 2a11 11 0 006 6l2-3 5 2v4a2 2 0 01-2 2A17 17 0 013 5a2 2 0 012-2z"/></svg></div>
  <div class="field tall"><label>Message</label><span>Type Your Message</span>
    <svg width="16" height="16" viewBox="0 0 24 24" fill="none" stroke="#333" stroke-width="1.8"><path d="M3 4h18v12H8l-5 4z"/><path d="M7 9h10M7 12h6"/></svg></div>
  <div class="talk">Let's Talk</div>
</div>
<div class="abs contact-frame"></div>
<div class="photo contact-photo" role="img" aria-label="Support agent with headset working at a desk"></div>

<!-- footer -->
<svg class="abs" style="left:0;top:3765px" width="1200" height="402" viewBox="0 0 1200 402">
  <defs><linearGradient id="foot" x1="0" x2="1" y1="0" y2="1"><stop offset="0" stop-color="#F0912C"/><stop offset=".6" stop-color="#F2A743"/><stop offset="1" stop-color="#F0912C"/></linearGradient></defs>
  <path d="M0 55 L470 0 L600 20 L1200 40 L1200 402 L0 402Z" fill="#B96A22"/>
  <path d="M0 55 L600 20 L1200 40 L1200 402 L0 402Z" fill="url(#foot)"/>
</svg>
<div class="abs foot-brand" style="top:3870px">
  <span class="mark"></span>
  <span class="name">FENWICK</span>
  <span class="sub">GRADING LTD</span>
</div>
<span class="social" style="left:119px"></span>
<span class="social" style="left:171px"></span>
<span class="social" style="left:224px"></span>
<span class="social" style="left:276px"></span>
<span class="social" style="left:329px"></span>

<div class="fcol" style="left:455px">
  <h5>OUR SERVICES</h5>
  <ul><li>Commercial</li><li>Residential</li><li>Landscape lighting</li><li>fiber optic installation</li></ul>
</div>
<div class="fcol" style="left:687px">
  <h5>MENUS</h5>
  <ul><li>&nbsp;Home</li><li>About Us</li><li>service</li><li>Landscape Lighting</li></ul>
</div>
<div class="fcol" style="left:898px">
  <h5>CONTACT</h5>
  <ul>
    <li class="ci"><svg width="20" height="24" viewBox="0 0 20 24" fill="#fff"><path d="M10 0a8 8 0 018 8c0 6-8 16-8 16S2 14 2 8a8 8 0 018-8zm0 5a3 3 0 100 6 3 3 0 000-6z"/></svg>USA</li>
    <li class="ci"><svg width="22" height="16" viewBox="0 0 24 18" fill="none" stroke="#fff" stroke-width="1.8"><rect x="1" y="1" width="22" height="16"/><path d="M1 1l11 8 11-8"/></svg>fenwickgrading@mailbox-example.net</li>
    <li class="ci"><svg width="22" height="22" viewBox="0 0 24 24" fill="none" stroke="#fff" stroke-width="1.8"><path d="M5 3h4l2 5-3 2a11 11 0 006 6l2-3 5 2v4a2 2 0 01-2 2A17 17 0 013 5a2 2 0 012-2z"/></svg>+0 (555) 010 22 33</li>
  </ul>
</div>
<div class="abs foot-rule"></div>
<div class="abs copy">© Copyrights 2024 by Fenwick Grading LTD &nbsp;- All rights reserved.</div>

</body>
</html>
```